Rultan Staffing Full Length Retractable Office Banner

I need a design for a full-length retractable banner and A-Frame Sign for each of my offices. I have included designs that have been incorporated into a poster and tri-fold as a sample. I would like to see a colorful eyecatching banner that focuses on people. Would like to see some diversity with men and woman and different races.
Rultan Staffing is a light industrial staffing firm. www.RultanStaffing.example

Target Market(s)

Job seekers looking for employment

Industry/Entity Type

Staffing / Recruiting

Font styles to use
Other font styles liked:
• Professional yet fun

Requirements
Must have
• Eye catching design with young hip vibe.
Nice to have
• primary colors with light industrial type jobs

```html
<!DOCTYPE html>
<html lang="en">
<head>
<meta charset="utf-8">
<title>Rultan Staffing Retractable Banner</title>
<link href="https://fonts.googleapis.com/css2?family=Oswald:wght@500;600&family=Roboto:wght@400;500;700&display=swap" rel="stylesheet">
<style>
  :root {
    --backdrop: #616161;
    --navy: #2d2b66;
    --red: #e42a2a;
    --green: #1f6b35;
    --yellow: #f2d214;
    --paper-top: #ffffff;
    --paper-bottom: #efefed;
  }
  * { margin: 0; padding: 0; box-sizing: border-box; }
  html, body {
    width: 1200px; height: 930px; overflow: hidden;
    background: var(--backdrop);
  }
  .banner {
    position: absolute;
    left: 413px; top: 25px;
    width: 374px; height: 880px;
    background: linear-gradient(180deg, var(--paper-top) 0%, var(--paper-bottom) 60%, #f6f6f4 100%);
    overflow: hidden;
    text-align: center;
  }
  .brand-name {
    position: absolute; left: 0; right: 0; top: 92px;
    font-family: "Roboto", sans-serif; font-weight: 500;
    font-size: 42px; color: var(--navy); letter-spacing: 0.5px;
  }
  .tagline { position: absolute; left: 0; right: 0; top: 244px; }
  .tagline-connecting {
    font-family: "Oswald", sans-serif; font-weight: 600;
    font-size: 58px; line-height: 62px; color: var(--navy);
    letter-spacing: 1px;
  }
  .tagline-people {
    font-family: "Roboto", sans-serif; font-size: 38px; line-height: 42px;
    color: var(--red);
  }
  .tagline-people strong { font-weight: 700; }
  .tagline-people span { font-weight: 400; }
  .tagline-with {
    font-family: "Roboto", sans-serif; font-weight: 400;
    font-size: 23px; line-height: 30px; color: var(--navy);
  }
  .tagline-orgs {
    font-family: "Oswald", sans-serif; font-weight: 500;
    font-size: 33px; line-height: 40px; color: var(--green);
  }
  .colour-rule {
    position: absolute; left: 0; top: 462px;
    display: flex; gap: 2px; width: 374px; height: 5px;
  }
  .colour-rule i { flex: 1; display: block; }
  .colour-rule .red { background: var(--red); }
  .colour-rule .green { background: var(--green); }
  .colour-rule .yellow { background: var(--yellow); }
  .colour-rule .navy { background: var(--navy); }
  .web-address {
    position: absolute; left: 0; right: 0; top: 491px;
    font-family: "Roboto", sans-serif; font-size: 15px;
    letter-spacing: 2.6px; color: var(--navy);
  }
  .web-address em { font-style: normal; color: var(--red); }
  .team-photo {
    position: absolute; left: 0; top: 540px;
    width: 374px; height: 340px;
    background:
      linear-gradient(180deg, rgba(246,246,244,1) 0%, rgba(246,246,244,0) 28%),
      linear-gradient(90deg, #8a7566 0%, #6a6f84 30%, #9a8c80 55%, #7f7d86 75%, #b9ac5a 90%, #6f6f78 100%);
  }
</style>
</head>
<body>
  <main class="banner">
    <div class="brand-name">Rultan Staffing</div>

    <div class="tagline">
      <div class="tagline-connecting">CONNECTING</div>
      <div class="tagline-people"><strong>GREAT</strong> <span>PEOPLE</span></div>
      <div class="tagline-with">WITH</div>
      <div class="tagline-orgs">GREAT ORGANIZATIONS!</div>
    </div>

    <div class="colour-rule"><i class="red"></i><i class="green"></i><i class="yellow"></i><i class="navy"></i></div>

    <div class="web-address">www.<em>RultanStaffing</em>.example</div>

    <div class="team-photo" role="img" aria-label="Photo of a diverse group of smiling men and women standing together"></div>
  </main>
</body>
</html>
```